High value cover design for an A4 ideation pad.

The product is NOT A BOOK.

It's an A4 ideation pad for professionals, designers and creators who handwrite their ideas. Visualise creators like Milo Varnet, Owen Plaskit and Gregor Lunwick in your mind's eye.

I'm looking for a cover design for the ideation pad. Both front and back.

It should look, feel and convey the following.

--> A handcrafted product experience

--> High value & Elegance

--> Inspiration

Mandatory --> See Uploaded Files --> Files 1, 5 & 6

Target Market(s)

- Designers

-Creative Professionals

- Entrepreneurs

who handwrite their ideas. Visualise creators like Milo Varnet, Owen Plaskit and Gregor Lunwick in your mind's eye.

Industry/Entity Type

Stationary

Font styles to use
Script
Other font styles liked:
• Calligraphy

Colors
fbed22

Requirements
Must have
• Title text - Quiet Kettle Notes

-Text in gold on brown leather background to convey high value for the front cover.

--> High value & Elegance

--> Inspiration

--> Should compel the customers to pick up and own the idea pad
Nice to have
• That's my take but other ideas are welcome
Should not have
• Must not convey

- low value

```html
<!DOCTYPE html>
<html lang="en">
<head>
<meta charset="utf-8">
<title>Quiet Kettle Notes — Ideation Pad Cover</title>
<link rel="stylesheet" href="https://fonts.googleapis.com/css2?family=Pinyon+Script&family=Playfair+Display:wght@700&display=swap">
<style>
  :root {
    --page-bg: #ecebee;
    --leather: #76583f;
    --leather-light: #85664b;
    --leather-deep: #4a3020;
    --quote-brown: #6e4e36;
    --gold-light: #fbed22;
    --gold-mid: #e0b52a;
    --gold-deep: #a87412;
  }
  html, body {
    margin: 0;
    width: 1200px;
    height: 941px;
    overflow: hidden;
    background: var(--page-bg);
  }
  .canvas {
    position: relative;
    width: 1200px;
    height: 941px;
  }
  .pad-cover {
    position: absolute;
    left: 296px;
    top: 40px;
    width: 608px;
    height: 861px;
    background: var(--leather);
    box-shadow: 0 6px 18px rgba(0,0,0,0.18);
    overflow: hidden;
  }
  .leather-pattern {
    position: absolute;
    inset: 0;
    background: radial-gradient(ellipse at 55% 40%, var(--leather-light) 0%, var(--leather) 70%);
  }
  .shatter {
    position: absolute;
    inset: 0;
    width: 100%;
    height: 100%;
  }
  .quote-mark {
    position: absolute;
    font-family: "Playfair Display", Georgia, serif;
    font-weight: 700;
    font-size: 150px;
    line-height: 1;
    color: var(--quote-brown);
    text-shadow: 0 2px 2px rgba(0,0,0,0.25), 0 -1px 0 rgba(255,255,255,0.12);
  }
  .quote-open { left: 112px; top: 290px; }
  .quote-close { left: 424px; top: 450px; }
  .cover-title {
    position: absolute;
    left: 150px;
    top: 300px;
    width: 300px;
    margin: 0;
    font-family: "Pinyon Script", cursive;
    font-weight: 400;
    text-align: center;
    line-height: 0.82;
    background: linear-gradient(180deg, var(--gold-light) 0%, var(--gold-mid) 45%, var(--gold-deep) 100%);
    -webkit-background-clip: text;
    background-clip: text;
    color: transparent;
    filter: drop-shadow(0 2px 1px rgba(40,20,5,0.5));
  }
  .cover-title span { display: block; }
  .title-line-one { font-size: 76px; padding-left: 40px; }
  .title-line-two { font-size: 62px; }
  .title-line-three { font-size: 76px; padding-right: 20px; }
</style>
</head>
<body>
<div class="canvas">
  <section class="pad-cover">
    <div class="leather-pattern" role="img" aria-label="Fine paisley and floral ornament pattern on brown leather"></div>
    <svg class="shatter" viewBox="0 0 608 861" preserveAspectRatio="none" role="img" aria-label="Dark shattered fragment corners, top left and bottom right">
      <defs>
        <linearGradient id="shatterTop" x1="0" y1="0" x2="1" y2="1">
          <stop offset="0" stop-color="#4a3020" stop-opacity="0.8"/>
          <stop offset="0.6" stop-color="#4a3020" stop-opacity="0.35"/>
          <stop offset="1" stop-color="#4a3020" stop-opacity="0"/>
        </linearGradient>
        <linearGradient id="shatterBottom" x1="1" y1="1" x2="0" y2="0">
          <stop offset="0" stop-color="#4a3020" stop-opacity="0.8"/>
          <stop offset="0.6" stop-color="#4a3020" stop-opacity="0.35"/>
          <stop offset="1" stop-color="#4a3020" stop-opacity="0"/>
        </linearGradient>
      </defs>
      <polygon points="0,0 300,0 200,150 110,260 30,280 0,270" fill="url(#shatterTop)"/>
      <polygon points="608,560 608,861 300,861 380,760 480,660" fill="url(#shatterBottom)"/>
    </svg>
    <span class="quote-mark quote-open" aria-hidden="true">&ldquo;</span>
    <h1 class="cover-title">
      <span class="title-line-one">Quiet</span>
      <span class="title-line-two">Kettle</span>
      <span class="title-line-three">Notes</span>
    </h1>
    <span class="quote-mark quote-close" aria-hidden="true">&rdquo;</span>
  </section>
</div>
</body>
</html>
```